Google Form Graphic to suit our Brand and industry

Create a graphic / image for us to put at the top of our client enquiry google form.
The image will be a section of an architectural home with our branding over the top. Preferably translucent.
The image must suit the shape of the google forms image, which is an elongated rectangle
#003d5d - brand colour

Target Market(s)

residential home owners, high end architectural homes

Industry/Entity Type

Residential construction

Colors
0054AA
0677BA
7BADD7
CADEEF
E8F1F8

Requirements
Must have
• our branding and a photo of an architectural home in the background

```html
<!DOCTYPE html>
<html lang="en">
<head>
<meta charset="utf-8">
<title>Vela Buildwork – Enquiry form header options</title>
<link rel="stylesheet" href="https://fonts.googleapis.com/css2?family=Montserrat:wght@600&family=Roboto:wght@400;500&display=swap">
<style>
  :root {
    --stage: #a0a0a0;
    --page: #e0eee0;
    --white: #ffffff;
    --navy: #003d5d;
    --accent-green: #3c8f3f;
    --accent-blue: #4a7fcf;
    --ink: #202124;
    --muted: #5f6368;
    --hairline: #c7c7c7;
    --card-line: #dadce0;
    --sky-light: #e8f1f8;
    --sky-mid: #7badd7;
    --sky-deep: #0677ba;
    --leaf: #6fae5a;
    --lagoon: #5cc4c0;
  }
  * { box-sizing: border-box; margin: 0; padding: 0; }
  html, body { width: 1200px; height: 820px; overflow: hidden; }
  body {
    background: var(--stage);
    font-family: "Roboto", Arial, sans-serif;
    color: var(--ink);
    position: relative;
  }
  .form-editor {
    position: absolute;
    top: 66px;
    width: 529px;
    height: 687px;
    background: var(--page);
    overflow: hidden;
  }
  .form-editor--tower { left: 48px; }
  .form-editor--village { left: 620px; }

  .tab-bar {
    position: absolute; left: 0; top: 0; width: 100%; height: 25px;
    background: var(--white);
    border-bottom: 1px solid #d7e2d7;
  }
  .tab {
    position: absolute; top: 7px;
    font-size: 8px; font-weight: 500; color: var(--ink);
    transform: translateX(-50%);
  }
  .tab--active { color: var(--accent-green); }
  .tab--questions { left: 210px; }
  .tab--responses { left: 260px; }
  .tab--settings { left: 307px; }
  .tab-indicator {
    position: absolute; left: 187px; top: 22px; width: 47px; height: 2.5px;
    background: var(--accent-green); border-radius: 2px 2px 0 0;
  }

  .header-banner {
    position: absolute; left: 48px; top: 31px; width: 419px; height: 105px;
    border-radius: 4px; overflow: hidden;
  }
  .header-banner svg { display: block; }
  .brand-name {
    font-family: "Montserrat", Arial, sans-serif;
    font-weight: 600;
    font-size: 17px;
    fill: var(--navy);
  }

  .card {
    position: absolute; left: 48px; width: 418px;
    background: var(--white);
    border-radius: 4px;
    border: 1px solid var(--card-line);
  }
  .card--title {
    top: 143px; height: 96px;
    border-top: 5px solid var(--accent-green);
    border-left: 3px solid var(--accent-blue);
  }
  .form-title {
    position: absolute; left: 10px; top: 14px;
    font-size: 18.5px; font-weight: 400; color: var(--ink);
  }
  .form-title-line {
    position: absolute; left: 10px; top: 37px; width: 391px; height: 1.5px;
    background: var(--accent-green);
  }
  .format-tools {
    position: absolute; left: 10px; top: 41px;
    display: flex; gap: 2px;
  }
  .format-tool {
    width: 20px; height: 18px; display: flex; align-items: center; justify-content: center;
    border-radius: 3px;
  }
  .format-tool--on { background: #e8eaed; }
  .form-description {
    position: absolute; left: 10px; top: 65px;
    font-size: 8px; color: var(--muted);
  }
  .form-description-line {
    position: absolute; left: 10px; top: 76px; width: 391px; height: 1px;
    background: var(--card-line);
  }

  .card--question { height: 74px; }
  .card--focused { border-left: 3px solid var(--accent-blue); }
  .question-label {
    position: absolute; left: 13px; top: 13px;
    font-size: 8.5px; color: var(--ink);
  }
  .card--focused .question-label,
  .card--focused .answer-hint,
  .card--focused .answer-line { left: 11px; }
  .required { color: #d93025; margin-left: 2px; }
  .answer-hint {
    position: absolute; left: 13px; top: 38px;
    font-size: 7.5px; color: var(--muted);
  }
  .answer-line {
    position: absolute; left: 13px; top: 51px; height: 0;
    border-top: 1px dotted #b0b0b0;
  }
  .answer-line--short { width: 195px; }
  .answer-line--long { width: 332px; }

  .q-name { top: 246px; }
  .q-email { top: 327px; }
  .q-address { top: 408px; }
  .q-phone { top: 489px; }
  .q-comments { top: 570px; }

  .tool-rail {
    position: absolute; left: 473px; top: 143px; width: 25px; height: 137px;
    background: var(--white);
    border-radius: 4px;
    border: 1px solid var(--card-line);
    display: flex; flex-direction: column; align-items: center;
    padding-top: 6px; gap: 6px;
  }
  .tool-rail svg { display: block; }
</style>
</head>
<body>

<!-- Option A: tower banner -->
<section class="form-editor form-editor--tower">
  <nav class="tab-bar">
    <span class="tab tab--active tab--questions">Questions</span>
    <span class="tab tab--responses">Responses</span>
    <span class="tab tab--settings">Settings</span>
    <span class="tab-indicator"></span>
  </nav>

  <div class="header-banner">
    <svg width="419" height="105" viewBox="0 0 419 105">
      <defs>
        <linearGradient id="towerSky" x1="0" y1="0" x2="1" y2="0">
          <stop offset="0" stop-color="var(--sky-light)"/>
          <stop offset="0.55" stop-color="#a9d8ea"/>
          <stop offset="1" stop-color="#6cc3de"/>
        </linearGradient>
        <linearGradient id="towerFacade" x1="0" y1="0" x2="1" y2="1">
          <stop offset="0" stop-color="#8fc7e4"/>
          <stop offset="1" stop-color="#2d6f93"/>
        </linearGradient>
      </defs>
      <rect width="419" height="105" fill="url(#towerSky)"/>
      <rect x="270" y="0" width="149" height="105" fill="url(#towerFacade)" opacity="0.7"
            role="img" aria-label="Photo of a glass office tower seen from below"/>
      <polygon points="0,0 150,0 116,53 154,105 0,105" fill="var(--navy)"/>
      <text class="brand-name" x="124" y="59" textLength="160" lengthAdjust="spacing">VELA BUILDWORK</text>
    </svg>
  </div>

  <div class="card card--title">
    <h1 class="form-title">Contact information</h1>
    <div class="form-title-line"></div>
    <div class="format-tools">
      <span class="format-tool format-tool--on"><svg width="10" height="10" viewBox="0 0 10 10"><text x="1.5" y="9" font-family="Roboto, sans-serif" font-weight="700" font-size="10" fill="#202124">B</text></svg></span>
      <span class="format-tool"><svg width="10" height="10" viewBox="0 0 10 10"><path d="M4 1.5h4M2 8.5h4M6 1.5L4 8.5" stroke="#5f6368" stroke-width="1.2" fill="none"/></svg></span>
      <span class="format-tool"><svg width="10" height="10" viewBox="0 0 10 10"><path d="M2.5 1v4a2.5 2.5 0 0 0 5 0V1M2 9h6" stroke="#5f6368" stroke-width="1.2" fill="none"/></svg></span>
      <span class="format-tool"><svg width="12" height="10" viewBox="0 0 12 10"><path d="M5 3H3a2 2 0 0 0 0 4h2M7 3h2a2 2 0 0 1 0 4H7M4 5h4" stroke="#5f6368" stroke-width="1.2" fill="none"/></svg></span>
      <span class="format-tool"><svg width="10" height="10" viewBox="0 0 10 10"><path d="M2 1.5h7M5.5 1.5L4 8.5M1 1l8 8" stroke="#5f6368" stroke-width="1.2" fill="none"/></svg></span>
    </div>
    <p class="form-description">Form description</p>
    <div class="form-description-line"></div>
  </div>

  <div class="card card--question card--focused q-name">
    <p class="question-label">Name<span class="required">*</span></p>
    <p class="answer-hint">Short answer text</p>
    <div class="answer-line answer-line--short"></div>
  </div>
  <div class="card card--question q-email">
    <p class="question-label">Email<span class="required">*</span></p>
    <p class="answer-hint">Short answer text</p>
    <div class="answer-line answer-line--short"></div>
  </div>
  <div class="card card--question q-address">
    <p class="question-label">Address<span class="required">*</span></p>
    <p class="answer-hint">Long answer text</p>
    <div class="answer-line answer-line--long"></div>
  </div>
  <div class="card card--question q-phone">
    <p class="question-label">Phone number</p>
    <p class="answer-hint">Short answer text</p>
    <div class="answer-line answer-line--short"></div>
  </div>
  <div class="card card--question q-comments">
    <p class="question-label">Comments</p>
    <p class="answer-hint">Long answer text</p>
    <div class="answer-line answer-line--long"></div>
  </div>

  <aside class="tool-rail">
    <svg width="14" height="16" viewBox="0 0 14 16"><circle cx="7" cy="8" r="5.5" stroke="#5f6368" stroke-width="1.1" fill="none"/><path d="M7 5v6M4 8h6" stroke="#5f6368" stroke-width="1.1"/></svg>
    <svg width="14" height="16" viewBox="0 0 14 16"><path d="M3 2h5l3 3v9H3z" stroke="#5f6368" stroke-width="1.1" fill="none"/><path d="M1 9h6M5 7l2 2-2 2" stroke="#5f6368" stroke-width="1.1" fill="none"/></svg>
    <svg width="14" height="16" viewBox="0 0 14 16"><path d="M1 4h7M4.5 4v9M8 8h5M10.5 8v5" stroke="#5f6368" stroke-width="1.6" fill="none"/></svg>
    <svg width="14" height="16" viewBox="0 0 14 16"><rect x="2" y="3" width="10" height="10" stroke="#5f6368" stroke-width="1.1" fill="none"/><path d="M3.5 11.5l2.5-3 2 2 1.5-1.5 1.5 2.5z" fill="#5f6368"/></svg>
    <svg width="14" height="16" viewBox="0 0 14 16"><rect x="1.5" y="4" width="11" height="8" stroke="#5f6368" stroke-width="1.1" fill="none"/><path d="M6 6v4l3-2z" fill="#5f6368"/></svg>
    <svg width="14" height="16" viewBox="0 0 14 16"><rect x="2" y="3" width="10" height="4.5" stroke="#5f6368" stroke-width="1.1" fill="none"/><rect x="2" y="8.5" width="10" height="4.5" stroke="#5f6368" stroke-width="1.1" fill="none"/></svg>
  </aside>
</section>

<!-- Option B: lakeside homes banner -->
<section class="form-editor form-editor--village">
  <nav class="tab-bar">
    <span class="tab tab--active tab--questions">Questions</span>
    <span class="tab tab--responses">Responses</span>
    <span class="tab tab--settings">Settings</span>
    <span class="tab-indicator"></span>
  </nav>

  <div class="header-banner">
    <svg width="419" height="105" viewBox="0 0 419 105">
      <defs>
        <linearGradient id="villageScene" x1="0" y1="0" x2="0.6" y2="1">
          <stop offset="0" stop-color="#cfe8d0"/>
          <stop offset="0.45" stop-color="var(--leaf)"/>
          <stop offset="1" stop-color="var(--lagoon)"/>
        </linearGradient>
      </defs>
      <rect width="419" height="105" fill="var(--white)"/>
      <polygon points="315,0 419,0 419,105 320,105 280,53" fill="url(#villageScene)"
               role="img" aria-label="Illustration of lakeside homes among trees reflected in water"/>
      <polygon points="0,0 150,0 116,53 154,105 0,105" fill="var(--navy)"/>
      <text class="brand-name" x="124" y="59" textLength="150" lengthAdjust="spacing">VELA BUILDWORK</text>
    </svg>
  </div>

  <div class="card card--title">
    <h1 class="form-title">Contact information</h1>
    <div class="form-title-line"></div>
    <div class="format-tools">
      <span class="format-tool format-tool--on"><svg width="10" height="10" viewBox="0 0 10 10"><text x="1.5" y="9" font-family="Roboto, sans-serif" font-weight="700" font-size="10" fill="#202124">B</text></svg></span>
      <span class="format-tool"><svg width="10" height="10" viewBox="0 0 10 10"><path d="M4 1.5h4M2 8.5h4M6 1.5L4 8.5" stroke="#5f6368" stroke-width="1.2" fill="none"/></svg></span>
      <span class="format-tool"><svg width="10" height="10" viewBox="0 0 10 10"><path d="M2.5 1v4a2.5 2.5 0 0 0 5 0V1M2 9h6" stroke="#5f6368" stroke-width="1.2" fill="none"/></svg></span>
      <span class="format-tool"><svg width="12" height="10" viewBox="0 0 12 10"><path d="M5 3H3a2 2 0 0 0 0 4h2M7 3h2a2 2 0 0 1 0 4H7M4 5h4" stroke="#5f6368" stroke-width="1.2" fill="none"/></svg></span>
      <span class="format-tool"><svg width="10" height="10" viewBox="0 0 10 10"><path d="M2 1.5h7M5.5 1.5L4 8.5M1 1l8 8" stroke="#5f6368" stroke-width="1.2" fill="none"/></svg></span>
    </div>
    <p class="form-description">Form description</p>
    <div class="form-description-line"></div>
  </div>

  <div class="card card--question card--focused q-name">
    <p class="question-label">Name<span class="required">*</span></p>
    <p class="answer-hint">Short answer text</p>
    <div class="answer-line answer-line--short"></div>
  </div>
  <div class="card card--question q-email">
    <p class="question-label">Email<span class="required">*</span></p>
    <p class="answer-hint">Short answer text</p>
    <div class="answer-line answer-line--short"></div>
  </div>
  <div class="card card--question q-address">
    <p class="question-label">Address<span class="required">*</span></p>
    <p class="answer-hint">Long answer text</p>
    <div class="answer-line answer-line--long"></div>
  </div>
  <div class="card card--question q-phone">
    <p class="question-label">Phone number</p>
    <p class="answer-hint">Short answer text</p>
    <div class="answer-line answer-line--short"></div>
  </div>
  <div class="card card--question q-comments">
    <p class="question-label">Comments</p>
    <p class="answer-hint">Long answer text</p>
    <div class="answer-line answer-line--long"></div>
  </div>

  <aside class="tool-rail">
    <svg width="14" height="16" viewBox="0 0 14 16"><circle cx="7" cy="8" r="5.5" stroke="#5f6368" stroke-width="1.1" fill="none"/><path d="M7 5v6M4 8h6" stroke="#5f6368" stroke-width="1.1"/></svg>
    <svg width="14" height="16" viewBox="0 0 14 16"><path d="M3 2h5l3 3v9H3z" stroke="#5f6368" stroke-width="1.1" fill="none"/><path d="M1 9h6M5 7l2 2-2 2" stroke="#5f6368" stroke-width="1.1" fill="none"/></svg>
    <svg width="14" height="16" viewBox="0 0 14 16"><path d="M1 4h7M4.5 4v9M8 8h5M10.5 8v5" stroke="#5f6368" stroke-width="1.6" fill="none"/></svg>
    <svg width="14" height="16" viewBox="0 0 14 16"><rect x="2" y="3" width="10" height="10" stroke="#5f6368" stroke-width="1.1" fill="none"/><path d="M3.5 11.5l2.5-3 2 2 1.5-1.5 1.5 2.5z" fill="#5f6368"/></svg>
    <svg width="14" height="16" viewBox="0 0 14 16"><rect x="1.5" y="4" width="11" height="8" stroke="#5f6368" stroke-width="1.1" fill="none"/><path d="M6 6v4l3-2z" fill="#5f6368"/></svg>
    <svg width="14" height="16" viewBox="0 0 14 16"><rect x="2" y="3" width="10" height="4.5" stroke="#5f6368" stroke-width="1.1" fill="none"/><rect x="2" y="8.5" width="10" height="4.5" stroke="#5f6368" stroke-width="1.1" fill="none"/></svg>
  </aside>
</section>

</body>
</html>
```